Firm Stationery Design

I need a design for stationery, including: Stationery First Page, Stationery Second Sheet, Envelope, Mailing Label for Flat Envelopes, and Business Cards

```html
<!DOCTYPE html>
<html lang="en">
<head>
<meta charset="utf-8">
<title>Hartwell Law LLC — Envelope</title>
<link rel="stylesheet" href="https://fonts.googleapis.com/css2?family=Montserrat:wght@400;800&display=swap">
<style>
  :root {
    --bg: #3a3a3a;
    --paper: #f7f7f5;
    --ink: #111111;
    --accent: #f39c0b;
    --shadow: rgba(0, 0, 0, 0.35);
  }
  * { margin: 0; padding: 0; box-sizing: border-box; }
  html, body {
    width: 1200px;
    height: 800px;
    overflow: hidden;
    background: var(--bg);
    font-family: "Montserrat", sans-serif;
  }
  .canvas {
    position: relative;
    width: 1200px;
    height: 800px;
  }
  .envelope {
    position: absolute;
    width: 700px;
    height: 330px;
    background: var(--paper);
    box-shadow: 0 12px 30px var(--shadow);
    overflow: hidden;
  }
  .envelope--front { left: 60px; top: 40px; }
  .envelope--back { left: 440px; top: 430px; }

  .brand {
    position: absolute;
    left: 40px;
    top: 36px;
    display: flex;
    align-items: center;
    gap: 10px;
  }
  .brand__mark {
    width: 18px;
    height: 18px;
    background: var(--accent);
  }
  .brand__name {
    font-weight: 800;
    font-size: 17px;
    letter-spacing: 0.5px;
    color: var(--ink);
    text-transform: uppercase;
  }
  .return-address {
    position: absolute;
    left: 40px;
    bottom: 36px;
    font-size: 11px;
    line-height: 1.45;
    color: var(--ink);
  }
  .front-panel {
    position: absolute;
    right: 0;
    top: 0;
    width: 330px;
    height: 100%;
  }

  .flap {
    position: absolute;
    left: 0;
    top: 0;
    width: 100%;
    height: 130px;
    background: var(--accent);
    border-radius: 0 0 26px 26px;
    display: flex;
    align-items: center;
    justify-content: center;
  }
  .flap__name {
    font-weight: 800;
    font-size: 24px;
    letter-spacing: 1px;
    color: var(--paper);
    text-transform: uppercase;
  }
</style>
</head>
<body>
  <main class="canvas">
    <section class="envelope envelope--front" aria-label="Envelope front">
      <div class="brand">
        <span class="brand__mark"></span>
        <span class="brand__name">Hartwell Law LLC</span>
      </div>
      <p class="return-address">Your address, City<br>State, Zip 1234</p>
      <svg class="front-panel" viewBox="0 0 330 330" preserveAspectRatio="none" aria-hidden="true">
        <rect x="0" y="0" width="170" height="330" fill="#111111"/>
        <rect x="210" y="0" width="70" height="330" fill="#f39c0b"/>
      </svg>
    </section>

    <section class="envelope envelope--back" aria-label="Envelope back">
      <div class="flap">
        <span class="flap__name">Hartwell Law LLC</span>
      </div>
    </section>
  </main>
</body>
</html>
```